Luxury Wine Label for New Startup Winery

We need a wine label for our new winery startup. We have worked with a local designer but do not feel the resulting label / logo have the elevation required to present our brand as a luxury wine. Our winery is called "Quailbrook Vineyards" and we are focused on extremely high quality hand crafted artisan and estate wines from the Pacific Northwest.
We would like to see designs that utilize a tree line, or other imagery that represents the "Quailbrook" part of our company name. Another interesting feature could be wood grain.
A logo will be required based on your design so please design with this in mind:
This logo should be consistent with the wine bottle label design, and should be representative of our high end exclusive wine while giving a sense of place (Oregon/ Pacific Northwest.)
I will supply an image of the design we received from our local designer, PLEASE NOTE: in general we do like wood grain and tree line concepts but feel the execution was poorly done.
ATTN: Logo design should be suitable for use on: Bottles (Red wine/rose/white wine), Bussiness cards, vehicle signage, business signage, etc
P.S.:
If you have a design that is not outside the box we are still interested in seeing it.
Label is for a burgundy style bottle with a label height of 3.5 - 4" and a width of 3.5-4"
any label <= 4"x4" and >=3.5"x3.5" will be acceptable:
HOWEVER Width should be greater than or equal to height due to the bottle format
Target Market(s)
Wine enthusiasts with adequate discretionary budgets to afford $100 bottles of wine.
Industry/Entity Type
Wine / Winery
Requirements
Must have
- A sense of luxury, a feel of exclusivity, and a theme consistent with our product and brand name
Nice to have
- Tree line, wood grain or other wood themes. Serif fonts
Should not have
- anything cheesy, off topic, hard to read script fonts or anything that makes the label hard to read from a few feet away or too busy

```html
<!DOCTYPE html>
<html lang="en">
<head>
<meta charset="utf-8">
<title>Quailbrook Vineyards – White Wine Label</title>
<link href="https://fonts.googleapis.com/css2?family=Cormorant+Garamond:wght@500&family=Pinyon+Script&display=swap" rel="stylesheet">
<style>
  :root {
    --page: #ffffff;
    --frame-line: #e3cfa0;
    --grain-light: #d9c3cc;
    --grain-mid: #8a5a6a;
    --grain-dark: #3e1a26;
    --panel: rgba(48, 22, 30, 0.93);
    --gold: #d6a52a;
    --gold-deep: #9c7418;
    --cream: #f3e6d8;
  }
  html, body {
    margin: 0;
    padding: 0;
    width: 1200px;
    height: 1200px;
    overflow: hidden;
    background: var(--page);
  }
  .label {
    position: relative;
    width: 1200px;
    height: 1200px;
  }
  .label__frame {
    position: absolute;
    left: 103px;
    top: 103px;
    width: 994px;
    height: 994px;
    box-sizing: border-box;
    border: 1.5px solid var(--frame-line);
    border-radius: 26px;
  }
  .label__woodgrain {
    position: absolute;
    left: 129px;
    top: 129px;
    width: 942px;
    height: 942px;
    border-radius: 10px;
    background:
      radial-gradient(ellipse 60% 45% at 45% 30%, rgba(62,26,38,0.55), transparent 70%),
      radial-gradient(ellipse 50% 40% at 70% 80%, rgba(217,195,204,0.5), transparent 70%),
      linear-gradient(135deg, var(--grain-mid) 0%, var(--grain-light) 35%, var(--grain-mid) 60%, var(--grain-dark) 100%);
  }
  .label__panel {
    position: absolute;
    left: 288px;
    top: 424px;
    width: 624px;
    height: 339px;
    background: var(--panel);
    border-top: 5px solid var(--gold);
    box-sizing: border-box;
  }
  .label__seal {
    position: absolute;
    left: 555px;
    top: 363px;
    width: 90px;
    height: 90px;
    border-radius: 50%;
    background: radial-gradient(circle, var(--gold) 55%, var(--gold-deep) 100%);
  }
  .label__name {
    position: absolute;
    left: 288px;
    width: 624px;
    text-align: center;
    margin: 0;
    font-family: "Cormorant Garamond", serif;
    font-weight: 500;
    font-size: 72px;
    line-height: 1;
    letter-spacing: 0.09em;
    color: var(--cream);
    text-transform: uppercase;
  }
  .label__name--first { top: 482px; }
  .label__name--second { top: 576px; }
  .label__variety {
    position: absolute;
    left: 288px;
    width: 624px;
    top: 685px;
    margin: 0;
    text-align: center;
    font-family: "Pinyon Script", cursive;
    font-size: 36px;
    line-height: 1;
    color: var(--cream);
  }
</style>
</head>
<body>
  <main class="label">
    <div class="label__frame"></div>
    <div class="label__woodgrain" role="img" aria-label="Close-up wood grain texture in plum and burgundy tones"></div>
    <section class="label__panel"></section>
    <div class="label__seal" aria-hidden="true"></div>
    <h1 class="label__name label__name--first">Quailbrook</h1>
    <p class="label__name label__name--second">Vineyards</p>
    <p class="label__variety">White Wine</p>
  </main>
</body>
</html>
```